Silver Bloom Marisol's Cleaning Service Business Cards Project

A business card with all contact details with logo design on there (already have a logo) eye catching Logo and contact info on one side, full logo on the back, must target upper class residential and corporate companies, fitness companies, still keep it on the feminine side of things , must look elegant

Target Market(s)

Upper class homes and corporate companies

Industry/Entity Type

Cleaning Service

Contact Information for Business Card

Name: Marisol Quenby
Position: Director
ABN: 31647209853
Email: marisolssilvercleaning@tidymail.example
Number: 0417906354

Font styles to use
Decorative

Colors

Designer to choose colors to be used in the design.

Requirements
Must have
• Available Sydney Wide, contact info and logo on one side, full logo on the back
Nice to have
• Professional appearance
Should not have
• Cheap advert looking stuff

```html
<!DOCTYPE html>
<html lang="en">
<head>
<meta charset="utf-8">
<title>Silver Bloom – Business Cards</title>
<link rel="stylesheet" href="https://fonts.googleapis.com/css2?family=Noto+Serif:wght@400;700&family=Arimo:wght@400&display=swap">
<style>
  :root {
    --backdrop: #3a3a3c;
    --card: #1d1d1e;
    --silver: #c9c9cb;
    --silver-bright: #e6e6e8;
    --silver-muted: #8d8d90;
    --edge: #9a9a9c;
  }
  * { box-sizing: border-box; margin: 0; padding: 0; }
  html, body {
    width: 1200px; height: 900px; overflow: hidden;
    background: var(--backdrop);
  }
  .canvas {
    width: 1200px; height: 900px;
    display: flex; flex-direction: column; align-items: center; justify-content: center;
    gap: 44px;
  }
  .card {
    width: 740px; height: 400px;
    background: var(--card);
    border-bottom: 3px solid var(--edge);
    position: relative;
    box-shadow: 0 10px 24px rgba(0,0,0,0.35);
  }
  .brand-name {
    font-family: "Noto Serif", serif;
    font-weight: 400;
    color: var(--silver);
    text-align: center;
    line-height: 1.2;
  }
  .brand-name .title { display: block; text-transform: uppercase; letter-spacing: 1px; }
  .brand-name .tagline { display: block; text-transform: uppercase; }
  .brand-dot {
    width: 14px; height: 14px; border-radius: 50%;
    background: var(--silver);
    margin: 0 auto 16px;
  }

  /* front */
  .card-front { display: flex; align-items: center; justify-content: center; }
  .card-front .title { font-size: 40px; }
  .card-front .tagline { font-size: 14px; letter-spacing: 5px; margin-top: 4px; }

  /* back */
  .card-back { display: flex; align-items: center; }
  .back-brand { width: 330px; padding-left: 40px; }
  .card-back .title { font-size: 29px; }
  .card-back .tagline { font-size: 10px; letter-spacing: 3px; margin-top: 4px; }
  .divider { width: 2px; height: 230px; background: var(--silver-muted); margin: 0 26px 0 20px; }
  .contact { color: var(--silver-bright); font-family: Arimo, sans-serif; }
  .contact-name { font-family: "Noto Serif", serif; font-weight: 700; font-size: 27px; letter-spacing: 0.5px; }
  .contact-role { font-size: 17px; color: var(--silver); margin-top: 2px; }
  .contact-abn { font-size: 19px; margin-top: 30px; letter-spacing: 0.5px; }
  .contact-line { display: flex; align-items: center; gap: 12px; font-size: 19px; margin-top: 14px; letter-spacing: 0.5px; }
  .contact-line.email { font-size: 16px; margin-top: 8px; letter-spacing: 0.2px; }
  .contact-line svg { flex: none; }
</style>
</head>
<body>
<main class="canvas">
  <section class="card card-front" aria-label="Card front">
    <div class="brand">
      <div class="brand-dot"></div>
      <p class="brand-name"><span class="title">Silver Bloom</span><span class="tagline">Marisol's Cleaning Service</span></p>
    </div>
  </section>

  <section class="card card-back" aria-label="Card back">
    <div class="back-brand">
      <div class="brand-dot"></div>
      <p class="brand-name"><span class="title">Silver Bloom</span><span class="tagline">Marisol's Cleaning Service</span></p>
    </div>
    <div class="divider"></div>
    <div class="contact">
      <p class="contact-name">Marisol Quenby</p>
      <p class="contact-role">Director</p>
      <p class="contact-abn">ABN : 31647209853</p>
      <p class="contact-line phone">
        <svg width="18" height="18" viewBox="0 0 24 24" aria-hidden="true"><path fill="#d6d6d8" d="M6.6 10.8a15.1 15.1 0 0 0 6.6 6.6l2.2-2.2a1 1 0 0 1 1-.25 11.4 11.4 0 0 0 3.6.57 1 1 0 0 1 1 1V20a1 1 0 0 1-1 1A17 17 0 0 1 3 4a1 1 0 0 1 1-1h3.5a1 1 0 0 1 1 1c0 1.25.2 2.45.57 3.6a1 1 0 0 1-.25 1z"/></svg>
        0417906354
      </p>
      <p class="contact-line email">
        <svg width="20" height="14" viewBox="0 0 20 14" aria-hidden="true"><rect x="1" y="1" width="18" height="12" fill="none" stroke="#d6d6d8" stroke-width="1.4"/><path d="M1 1l9 7 9-7" fill="none" stroke="#d6d6d8" stroke-width="1.4"/></svg>
        marisolssilvercleaning@tidymail.example
      </p>
    </div>
  </section>
</main>
</body>
</html>
```